Car rental website design for a UAE car rental company

This project is about creating a new website design for a car rental company located in Dubai (United Arab Emirates), I opened the same project a few months ago but I didn't receive a lot of appealing entries so I closed it but this time I am marking the project as guaranteed to avoid such situation again, if you have already provided a design before then please re-submit again on this project so that it is considered while reviewing all the designs

A few important things:

1- We need a simple non-complex design
2- The final deliverable would be 2 screens (PSD, JPEG ... etc), the first screen is for the home page and the second screen is for an internal page
3- The home page must have a section that end users can use to rent a car online directly from the home page instead of going into some inner pages
4- The current website is very old and not very appealing so avoid creating a similar design (www.crestvane-autos.example)
5- The name is Crestvane but the company rents normal cars (no Limousin cars will be rented) so avoid adding any fancy cars in the images/graphics used in the design, just normal end users cars
6- The expected pages would be: home, About us, Our team, Strategy, Contact us and links to social media pages
7- The attachments include the company's logo and some screens from other car rental companies that provide online rentals/payments

If you have any questions please feel free to ask and please note that we will need the designs urgently

Thanks

Target Market(s)

Dubai - United Arab Emirates

Industry/Entity Type

It Company

Number of Pages Required

2 page

Font styles to use
Sans Serif

Requirements
Must have
• Check the project details
Nice to have
Should not have

```html
<!DOCTYPE html>
<html lang="en">
<head>
<meta charset="utf-8">
<title>Crestvane Rent A Car</title>
<link href="https://fonts.googleapis.com/css2?family=Roboto+Condensed:wght@400&family=Roboto+Slab:wght@300;400&family=Open+Sans:wght@400;600&display=swap" rel="stylesheet">
<style>
:root{
  --brand:#a3133f;
  --grey:#8a8a8a;
  --text:#333;
  --panel:#dcdcdc;
  --header:#e6e6e6;
  --band:#f3f3f3;
}
*{box-sizing:border-box;margin:0;padding:0}
html,body{width:920px;height:1200px;overflow:hidden;background:#fff}
body{position:relative;font-family:'Roboto Slab',serif;color:var(--text);font-weight:300}
.abs{position:absolute}
.header{left:0;top:0;width:920px;height:80px;background:var(--header);border-bottom:2px solid var(--brand)}
.brand{left:62px;top:14px;display:flex;align-items:center;gap:8px}
.brand-box{width:54px;height:54px;border:2px solid var(--brand)}
.brand-name{font-size:28px;color:var(--grey);font-weight:400;line-height:1}
.brand-sub{font-size:14px;color:var(--grey);letter-spacing:3px;font-weight:400;margin-top:4px}
.social{display:flex;gap:6px}
.social span{width:18px;height:18px;border-radius:50%;background:#3a6fb8;display:block}
.social span:last-child{background:#c8352b}
.call{left:648px;top:8px;display:flex;align-items:center;gap:8px;color:var(--brand);font-size:15px;font-weight:400}
.nav{left:463px;top:54px;display:flex;gap:19px;font-size:13px;color:var(--grey);font-weight:300}
.nav .active{color:var(--brand)}
.hero{left:0;top:82px;width:920px;height:334px;background:linear-gradient(160deg,#6b6e72,#9ea4aa 45%,#4a4c50);border-bottom:3px solid var(--brand)}
.hero-title{left:67px;top:96px;font-family:'Roboto Condensed',sans-serif;color:#fff;font-size:25px;line-height:30px}
.booking{left:541px;top:82px;width:316px;height:330px;background:var(--brand)}
.booking-body{left:3px;top:33px;width:311px;height:294px;background:var(--panel)}
.tab{left:3px;top:6px;padding:6px 9px;background:var(--panel);color:#fff;font-size:13px;background:#8b8b8b}
.tab2{left:91px;top:9px;color:#fff;font-size:12px}
.bk{font-size:11px;color:#333;font-weight:400}
.step{width:19px;height:19px;border:1px solid var(--brand);background:#fff;text-align:center;font-size:12px;line-height:17px}
.field{height:21px;border:1px solid #999;background:#f1f1f1;font-size:10px;padding:4px 6px;font-weight:400}
.link{color:var(--brand);text-decoration:underline;font-size:11px;font-weight:400}
.help{width:16px;height:16px;border-radius:50%;background:#a5a5a5;color:#fff;font-size:9px;text-align:center;line-height:16px}
.chk{width:8px;height:8px;border:1px solid #555;display:inline-block;margin-right:4px}
.quote{left:745px;top:382px;width:103px;height:30px;background:var(--brand);color:#fff;font-size:13px;text-align:center;line-height:30px;font-weight:400}
.features{left:0;top:419px;width:920px;height:207px;background:var(--band);border-bottom:1px solid #e2e2e2}
.feature{width:200px;text-align:center}
.feature .ring{width:72px;height:72px;border-radius:50%;border:2px solid #999;margin:0 auto 18px;display:flex;align-items:center;justify-content:center}
.feature.on .ring{border-color:var(--brand)}
.feature h3{font-size:12px;font-weight:400;line-height:16px;color:#333}
.feature p{font-family:'Open Sans',sans-serif;font-size:11px;line-height:15.5px;margin-top:6px;color:#444}
.section-title{width:920px;text-align:center;font-size:15px;color:var(--grey)}
.section-title b{color:var(--brand);font-weight:400}
.rule{border-top:1px dashed #999;height:0}
.car{width:170px;height:88px;border-radius:40px 50px 18px 18px}
.price{width:200px;text-align:center;font-family:'Roboto Condensed',sans-serif;font-size:13px;color:#333}
.shade{left:65px;width:790px;height:8px;background:radial-gradient(ellipse at top,rgba(0,0,0,.08),transparent 70%)}
.copy{left:90px;width:740px;text-align:center;font-size:11px;line-height:16.8px;color:#333;font-weight:300}
.footer{left:0;top:1155px;width:920px;height:45px;background:var(--brand);color:#fff}
.fnav{left:62px;top:15px;display:flex;gap:14px;font-size:11.5px}
.fright{left:666px;top:16px;font-family:'Open Sans',sans-serif;font-size:10.5px;font-weight:600}
</style>
</head>
<body>
<header class="abs header">
  <div class="abs brand"><span class="brand-box"></span><div><div class="brand-name">Crestvane</div><div class="brand-sub">Rent A Car</div></div></div>
  <div class="abs social" style="left:463px;top:14px"><span></span><span></span><span></span><span></span></div>
  <div class="abs call">
    <svg width="28" height="30" viewBox="0 0 28 30"><path d="M4 16a10 10 0 0 1 20 0" fill="none" stroke="#777" stroke-width="3"/><rect x="2" y="14" width="6" height="9" rx="2" fill="var(--brand)"/><rect x="20" y="14" width="6" height="9" rx="2" fill="var(--brand)"/><path d="M23 23q0 5-7 5" fill="none" stroke="#777" stroke-width="2"/></svg>
    Call us at +971 4 555 0182
  </div>
  <nav class="abs nav"><span class="active">HOME</span><span>ABOUT US</span><span>OUR TEAM</span><span>STRATEGY</span><span>CONTACT US</span></nav>
</header>

<section class="abs hero" role="img" aria-label="Silver family sedan parked on an asphalt road"></section>
<h1 class="abs hero-title" style="font-weight:400">Experience An Extra Mile of comfort,<br>pleasure and leisure From the best</h1>

<form class="abs booking">
  <div class="abs tab">Book A Car</div>
  <div class="abs tab2">View / Modify / Cancel A Reservation</div>
  <div class="abs booking-body"></div>
</form>
<div class="abs step" style="left:546px;top:124px">1</div>
<div class="abs bk" style="left:577px;top:125px">Pick-up Location &nbsp;(City, State or Airport Code</div>
<div class="abs link" style="left:578px;top:143px">Previous Searches</div>
<div class="abs field" style="left:577px;top:161px;width:261px">Dubai Airport - Terminal 3</div>
<div class="abs link" style="left:578px;top:188px">Help me find a rental location</div>
<div class="abs bk" style="left:577px;top:208px"><span class="chk"></span>Return car to a different Crestvane Location</div>
<div class="abs help" style="left:805px;top:207px">?</div>
<div class="abs step" style="left:546px;top:234px">2</div>
<div class="abs bk" style="left:577px;top:235px">Pick-up Date &amp; Time</div>
<div class="abs field" style="left:577px;top:254px;width:128px">26/03/2015</div>
<div class="abs field" style="left:709px;top:254px;width:128px">16:00</div>
<div class="abs bk" style="left:577px;top:284px">Return Date &amp; Time</div>
<div class="abs field" style="left:577px;top:302px;width:128px">26/03/2015</div>
<div class="abs field" style="left:709px;top:302px;width:128px">16:00</div>
<div class="abs bk" style="left:577px;top:333px">Hire Car Type</div>
<div class="abs field" style="left:577px;top:351px;width:128px">Automatic</div>
<div class="abs bk" style="left:712px;top:354px"><span class="chk"></span>Apply a discount Code</div>
<div class="abs help" style="left:836px;top:351px">?</div>
<div class="abs quote">Get A Quote</div>

<section class="abs features">
  <div class="abs feature on" style="left:54px;top:24px">
    <div class="ring"><svg width="46" height="34" viewBox="0 0 46 34"><path d="M4 14l5-9h18l5 9v8H4z" fill="var(--brand)"/><path d="M14 22l5-8h18l5 8v8H14z" fill="var(--brand)" stroke="var(--band)" stroke-width="2"/></svg></div>
    <h3>Wide Range Of Vehicles For City<br>Driving or SUV's For Trips</h3>
    <p>Lorem ipsum dolor sit<br>aonsectetuer adipiscing elied<br>diam nonummy</p>
  </div>
  <div class="abs feature" style="left:270px;top:24px">
    <div class="ring"><svg width="34" height="34" viewBox="0 0 34 34"><path d="M6 4h12l12 12-12 14L4 16z" fill="#8a8a8a"/><circle cx="12" cy="11" r="2.5" fill="#fff"/></svg></div>
    <h3>Special 10% Discount For New<br>Customers On The First Rent</h3>
    <p>Lorem ipsum dolor sit<br>aonsectetuer adipiscing elied<br>diam nonummy</p>
  </div>
  <div class="abs feature" style="left:476px;top:24px">
    <div class="ring"><svg width="34" height="36" viewBox="0 0 34 36"><circle cx="10" cy="7" r="4" fill="#8a8a8a"/><rect x="12" y="5" width="16" height="4" fill="#8a8a8a"/><path d="M4 22l4-8h18l4 8v9H4z" fill="#8a8a8a"/></svg></div>
    <h3>Long Term Car<br>Rentals</h3>
    <p>Lorem ipsum dolor sit<br>aonsectetuer adipiscing elied<br>diam nonummy</p>
  </div>
  <div class="abs feature" style="left:681px;top:24px">
    <div class="ring"><svg width="34" height="34" viewBox="0 0 34 34"><path d="M12 6L4 13l8 7v-4c8 0 13 3 13 11 4-11-3-16-13-16z" fill="#8a8a8a"/></svg></div>
    <h3>Buyback Option After<br>Lease Term</h3>
    <p>Lorem ipsum dolor sit<br>aonsectetuer adipiscing elied<br>diam nonummy</p>
  </div>
  <svg class="abs" style="left:32px;top:222px" width="10" height="16" viewBox="0 0 10 16"><path d="M8 1L2 8l6 7" fill="none" stroke="#ccc" stroke-width="1.5"/></svg>
  <svg class="abs" style="left:878px;top:222px" width="10" height="16" viewBox="0 0 10 16"><path d="M2 1l6 7-6 7" fill="none" stroke="#ccc" stroke-width="1.5"/></svg>
</section>

<h2 class="abs section-title" style="top:649px;font-weight:300">Grab the <b>Best Deal Today</b></h2>
<div class="abs rule" style="left:328px;top:673px;width:264px"></div>
<div class="abs car" style="left:74px;top:697px;background:linear-gradient(160deg,#e2e4e6,#9b9fa3)" role="img" aria-label="Silver sedan"></div>
<div class="abs car" style="left:284px;top:697px;background:linear-gradient(160deg,#e8433d,#a8121a)" role="img" aria-label="Red sedan"></div>
<div class="abs car" style="left:478px;top:697px;background:linear-gradient(160deg,#e2e4e6,#9b9fa3)" role="img" aria-label="Silver sedan"></div>
<div class="abs car" style="left:686px;top:697px;background:linear-gradient(160deg,#e8433d,#a8121a)" role="img" aria-label="Red sedan"></div>
<div class="abs price" style="left:58px;top:795px;color:var(--brand)">From Only AED 1100 p/m</div>
<div class="abs price" style="left:260px;top:797px">From Only AED 1100 p/m</div>
<div class="abs price" style="left:462px;top:795px">From Only AED 1100 p/m</div>
<div class="abs price" style="left:661px;top:797px">From Only AED 1100 p/m</div>
<div class="abs shade" style="top:834px"></div>

<h2 class="abs section-title" style="top:864px;font-weight:300">Welcome to Crestvane <b>Rent A Car</b></h2>
<div class="abs rule" style="left:280px;top:888px;width:360px"></div>
<p class="abs copy" style="top:893px">As Dubai is expected to welcome millions of tourists and visitors, car rental industry is believed to escalate more rapidly in the region. Over the past five years, demands for car rentals in Dubai has been augmenting at a healthy pace and is currently registering a growth rate of 20 to 25 percent per year. The swift economic growth and the number. Crestvane was established to bring comfort and pleasure to all its clients. First rate service plus highly maintained and top...</p>
<div class="abs section-title" style="top:966px;font-size:12px;color:#222;font-weight:400">Read More</div>
<div class="abs shade" style="top:1004px"></div>

<h2 class="abs section-title" style="top:1035px;font-weight:300">Our <b>Mission</b></h2>
<div class="abs rule" style="left:320px;top:1059px;width:280px"></div>
<p class="abs copy" style="top:1071px;left:80px;width:760px">To be one of the leading auto leasing company in the fast growing economy and tourism industry of the emirate of Dubai &amp; play alongside with the major car rental companies in the globe.<br><span style="display:block;margin-top:3px">Crestvane vows to deliver comfort, luxury &amp; satisfaction to all our clients by providing them professional, hassle-free and first class service.</span></p>

<footer class="abs footer">
  <nav class="abs fnav"><span>HOME</span><span>ABOUT US</span><span>OUR TEAM</span><span>STRATEGY</span><span>CONTACT US</span></nav>
  <div class="abs social" style="left:511px;top:13px"><span style="border:2px solid #fff"></span><span style="border:2px solid #fff"></span><span style="border:2px solid #fff"></span><span style="border:2px solid #fff"></span></div>
  <div class="abs fright">© 2015 Crestvane. All Rights Reserved</div>
</footer>
</body>
</html>
```